Security Special email compelling potential customers to call

I need a email designed that will go out to security dealers. A security dealer is a company that installs a security system for a homeowner to be monitored by a security company. To see the companies we are targeting go to http://www.plorvexguard.com/ or http://www.tandovelsiren.com/ . What we provide to these companies is the signs, aluminum stakes and decals. We want a flyer that states they can recieve free shipping on their entire order and to call for details. I have included picture files of signs and stakes That I had a professional photographer take. I have also included the last email marketing flyer we created so you could see the bones of what we want. ***NOTE*** We don't want the flyer to look like the one I have uploaded I want you to design something that will compel our target customers call us.

This program will not let me upload the hi-rez files. Please download them here: https://stickerquarry.filedrop.example/d-k7pq42ffa1930b2ee

Target Market(s)

Security dealers

Industry/Entity Type

Security

Colors

Designer to choose colors to be used in the design.

Requirements
Must have
• My phone number and a compelling message
Nice to have
• Use the pictures I sent

```html
<!DOCTYPE html>
<html lang="en">
<head>
<meta charset="utf-8">
<title>Free Shipping – The Sticker Quarry</title>
<link rel="stylesheet" href="https://fonts.googleapis.com/css2?family=Archivo+Black&family=Arimo:wght@400;500;700&family=Montserrat:wght@400;600&display=swap">
<style>
  :root {
    --yellow: #f7ea00;
    --ink: #231f20;
    --white: #ffffff;
    --page: #e4e4e0;
    --grey: #5a5a5a;
    --link: #1a6fc9;
    --tag-red: #e63323;
    --brand-blue: #1d4f91;
    --photo-top: #7c7f80;
    --photo-mid: #a7a9a4;
    --photo-low: #d6d4cc;
  }
  * { margin: 0; padding: 0; box-sizing: border-box; }
  html, body { width: 1200px; height: 2683px; overflow: hidden; }
  body { background: var(--page); font-family: "Arimo", Arial, sans-serif; color: var(--ink); }
  .canvas { position: relative; width: 1200px; height: 2683px; }
  .abs { position: absolute; }
  .center-text { left: 0; width: 1200px; text-align: center; }

  .palette-title { top: 45px; font-family: "Montserrat", sans-serif; font-weight: 600; font-size: 16px; }
  .palette { top: 80px; left: 529px; display: flex; gap: 14px; }
  .swatch { width: 43px; height: 43px; }
  .swatch--yellow { background: var(--yellow); }
  .swatch--ink { background: var(--ink); }
  .swatch--white { background: var(--white); }
  .contact-note { top: 166px; font-family: "Montserrat", sans-serif; font-size: 17px; color: #333; }
  .contact-note a { color: var(--link); }

  .email { left: 193px; top: 216px; width: 814px; height: 2282px; background: var(--white); box-shadow: 0 18px 30px -20px rgba(0,0,0,.25); }

  .brand { left: 227px; top: 240px; display: flex; align-items: center; gap: 12px; }
  .brand__mark { width: 34px; height: 34px; background: var(--brand-blue); }
  .brand__name { font-weight: 700; font-size: 32px; color: var(--brand-blue); }
  .social-top { left: 838px; top: 244px; display: flex; gap: 6px; }
  .social-top span { width: 41px; height: 41px; border-radius: 50%; background: #2a6db6; }
  .social-top span:nth-child(2) { background: #2aa9e0; }
  .social-top span:nth-child(3) { background: #e2452c; }

  .hero { left: 193px; top: 314px; }
  .hero__title { top: 706px; font-weight: 700; font-size: 33px; line-height: 37px; }

  .shipping-tag { left: 562px; top: 850px; width: 90px; height: 130px; background: var(--tag-red); transform: rotate(-14deg); border-radius: 6px 6px 4px 4px; }

  .headline { top: 1000px; font-family: "Archivo Black", sans-serif; font-size: 45px; line-height: 60px; text-transform: uppercase; }
  .order-btn { left: 501px; top: 1261px; width: 262px; height: 71px; background: var(--yellow); display: flex; align-items: center; justify-content: center; font-weight: 700; font-size: 23px; color: var(--ink); text-decoration: none; }
  .fine-print { top: 1356px; font-size: 21px; line-height: 30px; color: var(--grey); }

  .call-frame { left: 415px; top: 1450px; width: 393px; height: 454px; border: 3px solid var(--yellow); }
  .call-panel { left: 374px; top: 1463px; }
  .call-panel__icon { left: 540px; top: 1516px; width: 118px; height: 118px; border-radius: 50%; background: var(--yellow); }
  .call-panel__label { top: 1646px; left: 374px; width: 477px; text-align: center; font-weight: 700; font-size: 30px; color: var(--white); }
  .call-panel__phone { top: 1700px; left: 374px; width: 477px; text-align: center; font-family: "Archivo Black", sans-serif; font-size: 42px; color: var(--yellow); }
  .call-frame__note { top: 1822px; left: 415px; width: 393px; text-align: center; font-weight: 700; font-size: 19px; line-height: 27px; }

  .lead-time { top: 1954px; font-size: 39px; line-height: 45px; font-weight: 500; }
  .lead-time strong { font-family: "Archivo Black", sans-serif; font-weight: 400; font-size: 37px; }
  .site-link { left: 415px; top: 2150px; }
  .site-link__text { top: 2203px; font-weight: 700; font-size: 28px; }

  .footer-rule { left: 259px; top: 2319px; width: 647px; border-top: 1px dashed #c8c8c8; }
  .footer-item { display: flex; align-items: center; gap: 14px; font-size: 17px; }
  .footer-item svg { flex: none; }
  .footer-phone { left: 287px; top: 2356px; }
  .footer-web { left: 287px; top: 2410px; }
  .footer-social { left: 777px; top: 2356px; display: flex; gap: 9px; }
  .footer-social span { width: 39px; height: 39px; border-radius: 50%; border: 2px solid var(--ink); }
  .copyright { left: 560px; width: 355px; text-align: right; top: 2418px; font-weight: 700; font-size: 16px; }
</style>
</head>
<body>
<div class="canvas">
  <p class="abs center-text palette-title">Using Color this designs</p>
  <div class="abs palette">
    <span class="swatch swatch--yellow"></span>
    <span class="swatch swatch--ink"></span>
    <span class="swatch swatch--white"></span>
  </div>
  <p class="abs center-text contact-note">For anything about this mail you can contract us by <a href="#">click this link.</a></p>

  <div class="abs email"></div>

  <div class="abs brand">
    <span class="brand__mark"></span>
    <span class="brand__name">The Sticker Quarry</span>
  </div>
  <div class="abs social-top"><span></span><span></span><span></span></div>

  <svg class="abs hero" width="814" height="530" viewBox="0 0 814 530">
    <defs>
      <clipPath id="hero-shape">
        <path d="M0,0 H814 V276 C814,425 620,527 407,527 C194,527 0,425 0,276 Z"/>
      </clipPath>
      <linearGradient id="hero-photo" x1="0" y1="0" x2="0" y2="1">
        <stop offset="0" stop-color="var(--photo-top)"/>
        <stop offset=".5" stop-color="var(--photo-mid)"/>
        <stop offset="1" stop-color="var(--photo-low)"/>
      </linearGradient>
    </defs>
    <g clip-path="url(#hero-shape)">
      <rect width="814" height="530" fill="url(#hero-photo)" role="img" aria-label="Photo of a house porch with a home security yard sign on an aluminum stake"/>
      <rect y="369" width="814" height="118" fill="#f7ea00" opacity=".92"/>
    </g>
  </svg>
  <p class="abs center-text hero__title">Serving The Security Industry<br>Since 1983</p>

  <div class="abs shipping-tag" role="img" aria-label="Red hanging sale tag announcing free shipping"></div>

  <h1 class="abs center-text headline">Receive free<br>shipping on your<br>security package<br>order!</h1>
  <a class="abs order-btn" href="#">Order Now</a>
  <p class="abs center-text fine-print">Within the continental United States<br>(Minumums Apply)</p>

  <div class="abs call-frame"></div>
  <svg class="abs call-panel" width="477" height="343" viewBox="0 0 477 343">
    <polygon points="0,35 477,0 477,320 0,343" fill="#231f20"/>
  </svg>
  <div class="abs call-panel__icon" role="img" aria-label="Customer support headset icon"></div>
  <p class="abs call-panel__label">CALL FOR DETAILS</p>
  <p class="abs call-panel__phone">1-800-555-0147</p>
  <p class="abs call-frame__note">Why wait 3-4 weeks for your<br>products to be produced?</p>

  <p class="abs center-text lead-time">We currently ship<br><strong>security signs &amp; decals</strong><br>in 9 working days<br>after&nbsp; PDF proof approval!</p>
  <svg class="abs site-link" width="370" height="80" viewBox="0 0 370 80">
    <path d="M2,22 V76 H48 M322,76 H368 V22 H218 M152,22 H2" fill="none" stroke="#f7ea00" stroke-width="3"/>
    <path d="M170,14 L200,2 L190,30 L184,18 Z M184,18 L200,2" fill="none" stroke="#231f20" stroke-width="2.5" stroke-linejoin="round"/>
  </svg>
  <p class="abs center-text site-link__text">stickerquarry.com</p>

  <div class="abs footer-rule"></div>
  <div class="abs footer-item footer-phone">
    <svg width="36" height="36" viewBox="0 0 36 36"><path d="M12,4 C6,6 4,12 6,20 C9,28 15,32 22,32 L24,26 L18,23 L15,26 C12,23 10,18 11,13 L15,11 L14,4 Z" fill="#231f20"/></svg>
    <span>(800) 555-0147</span>
  </div>
  <div class="abs footer-item footer-web">
    <svg width="36" height="36" viewBox="0 0 36 36"><circle cx="18" cy="18" r="16" fill="none" stroke="#231f20" stroke-width="2"/><rect x="10" y="12" width="16" height="12" fill="none" stroke="#231f20" stroke-width="2"/><path d="M10,12 L18,19 L26,12" fill="none" stroke="#231f20" stroke-width="2"/></svg>
    <span>stickerquarry.com</span>
  </div>
  <div class="abs footer-social"><span></span><span></span><span></span></div>
  <p class="abs copyright">Copyright 2016 The Sticker Quarry</p>
</div>
</body>
</html>
```